Creative, fresh business card design for Ripplecraft Facades

We need a fresh, creative business card design for Ripplecraft Facades. We are the manufacturer of Ripplecraft Facades in Australia. Wall panels are 2400 x 1200mm panels made from MDF and feature 3D patterns on the face of the panel. The colours to be used are green, silver/grey and white RGB
Red 187
Green 207
Blue 65.

An idea is to possibly use a watermark of one of our designs as a background (like on the "Grids" design on the left hand side of page 2 of our brochure).

Target Market(s)

Interior designers, architects, builders and home renovators

Industry/Entity Type

Business

Contact Information for Business Card

Details to go on the card are:
Our logo (attached),
Slogan: "Decorative panels for interiors and exteriors",
Contact name,
Position,
Mobile phone number,
Business address,
Business phone,
Business fax,
Website and
Email address.

I have attached a few images of our panels and our brochure for reference.

The colours of the business card should feature our logo colours which are: RGB
Red 187
Green 207
Blue 65

Requirements
Must have
• Very modern fonts and design. Some of the designs shown especially the "Prisms" design which is a popular design.
Nice to have
• Creative but simple design. Very contemporary.
Should not have
• Anything ornate or old fashioned.

```html
<!DOCTYPE html>
<html lang="en">
<head>
<meta charset="utf-8">
<title>Ripplecraft Facades – Business Card</title>
<link rel="stylesheet" href="https://fonts.googleapis.com/css2?family=PT+Sans:wght@400;700&display=swap">
<style>
  :root {
    --backdrop: #1f1f1f;
    --card-white: #ffffff;
    --card-shade: #f1f1f1;
    --brand-green: rgb(187, 207, 65);
    --ink-dark: #4a4a4a;
    --ink-grey: #8c8c8c;
    --faint-block: #f0f0f0;
  }
  html, body {
    margin: 0;
    width: 1200px;
    height: 1000px;
    overflow: hidden;
    background: var(--backdrop);
    font-family: "PT Sans", sans-serif;
  }
  .business-card {
    position: absolute;
    left: 150px;
    top: 240px;
    width: 900px;
    height: 520px;
    border-radius: 34px;
    background: linear-gradient(135deg, var(--card-white) 45%, var(--card-shade) 100%);
    overflow: hidden;
  }
  .faint-block {
    position: absolute;
    right: -40px;
    top: 250px;
    width: 420px;
    height: 320px;
    background: var(--faint-block);
    opacity: 0.7;
  }
  .brand {
    position: absolute;
    left: 70px;
    top: 92px;
    display: flex;
    align-items: center;
    gap: 16px;
  }
  .brand-square {
    width: 54px;
    height: 54px;
    background: var(--brand-green);
  }
  .brand-name {
    font-size: 32px;
    font-weight: 700;
    color: var(--brand-green);
    letter-spacing: 0.5px;
  }
  .slogan {
    position: absolute;
    left: 140px;
    top: 150px;
    font-size: 15px;
    color: var(--ink-grey);
    letter-spacing: 1.5px;
  }
  .accent-line {
    position: absolute;
    left: 70px;
    right: 0;
    top: 236px;
    height: 2px;
    background: var(--brand-green);
  }
  .person-name {
    position: absolute;
    left: 70px;
    top: 190px;
    margin: 0;
    font-size: 34px;
    font-weight: 700;
    color: var(--ink-dark);
  }
  .person-name .surname { color: var(--brand-green); }
  .person-role {
    position: absolute;
    left: 70px;
    top: 244px;
    font-size: 20px;
    font-weight: 700;
    color: var(--ink-grey);
  }
  .contact-list {
    position: absolute;
    left: 70px;
    top: 286px;
    margin: 0;
    padding: 0;
    list-style: none;
    font-size: 20px;
    color: var(--ink-dark);
  }
  .contact-list li {
    display: flex;
    align-items: center;
    gap: 16px;
    height: 30px;
  }
  .contact-list li.gap-before { margin-top: 22px; }
  .contact-icon { width: 18px; height: 18px; fill: var(--ink-dark); }
  .web-accent { color: var(--brand-green); }
</style>
</head>
<body>
  <main class="business-card">
    <div class="faint-block"></div>

    <div class="brand">
      <div class="brand-square"></div>
      <span class="brand-name">Ripplecraft Facades</span>
    </div>
    <div class="slogan">decorative panels for interiors &amp; exteriors</div>

    <h1 class="person-name">Daniel <span class="surname">Hartley</span></h1>
    <div class="accent-line"></div>
    <div class="person-role">Director</div>

    <ul class="contact-list">
      <li>
        <svg class="contact-icon" viewBox="0 0 18 18" aria-hidden="true"><rect x="5" y="1" width="8" height="16" rx="1.5"/><rect x="6.5" y="3" width="5" height="10" fill="#fff"/></svg>
        +61 400 218 754
      </li>
      <li>
        <svg class="contact-icon" viewBox="0 0 18 18" aria-hidden="true"><path d="M4 2l3 0 1.5 4-2 1.5c1 2 2.5 3.5 4.5 4.5l1.5-2 4 1.5v3c0 1-1 1.5-2 1.5C8 16 2 10 2 4c0-1 .5-2 2-2z"/></svg>
        +61 3 9021 4470
      </li>
      <li>
        <svg class="contact-icon" viewBox="0 0 18 18" aria-hidden="true"><rect x="4" y="2" width="10" height="5"/><rect x="1" y="7" width="16" height="9" rx="1.5"/><rect x="4" y="10" width="10" height="2" fill="#fff"/></svg>
        +61 3 9021 4471
      </li>
      <li class="gap-before">
        <svg class="contact-icon" viewBox="0 0 18 18" aria-hidden="true"><rect x="1" y="4" width="16" height="11"/><path d="M1.5 4.5L9 10l7.5-5.5" stroke="#fff" stroke-width="1.5" fill="none"/></svg>
        daniel@ripplecraft.example
      </li>
      <li>
        <svg class="contact-icon" viewBox="0 0 18 18" aria-hidden="true"><circle cx="10" cy="7" r="5" fill="none" stroke="#4a4a4a" stroke-width="2.2"/><path d="M6.5 10.5L2 15" stroke="#4a4a4a" stroke-width="2.6"/></svg>
        <span>www.<span class="web-accent">ripplecraft</span>.example</span>
      </li>
    </ul>
  </main>
</body>
</html>
```